Tevlora website

Web design for small consulting firm
It can be simple, easy to find approach

The primary use is business to business for

a. people wanting to find out a bit more of us after receiving a business card
b. Search words to draw people from search engines to us

Target Market(s)

Senior staff of large companies, in their work capacity
MD / CEO / CFO , directors, etc.

Industry/Entity Type

Business

Colors
ffffff
f79020
faa54b
33a6d7

```html
<!DOCTYPE html>
<html lang="en">
<head>
<meta charset="utf-8">
<title>Tevlora Insight</title>
<link href="https://fonts.googleapis.com/css2?family=Questrial&family=Open+Sans:wght@400;600;700&display=swap" rel="stylesheet">
<style>
:root{
  --blue:#0b78ba;
  --blue-dark:#0a62a0;
  --blue-light:#33a6d7;
  --orange:#f79020;
  --orange-soft:#faa54b;
  --white:#ffffff;
  --grey-bg:#f2f2f2;
  --band:#ececec;
  --text:#666666;
  --rule:#dcdcdc;
}
*{margin:0;padding:0;box-sizing:border-box}
html,body{width:1200px;height:2230px;overflow:hidden;background:var(--white)}
body{position:relative;font-family:"Open Sans",Verdana,sans-serif;color:var(--text)}
.abs{position:absolute}
.topline{left:0;top:0;width:1200px;height:5px;background:var(--orange)}
.brand{left:89px;top:50px;display:flex;align-items:center;gap:10px;font-family:"Open Sans",sans-serif;font-weight:700;color:var(--blue);font-size:40px;letter-spacing:-0.5px;line-height:1}
.brand .dot{width:16px;height:16px;border-radius:50%;background:var(--orange)}
.brand small{display:block;font-size:18px;letter-spacing:6px;margin-top:6px}
.social{display:flex;gap:6px}
.social span{width:27px;height:27px;border-radius:50%;display:block}
.social.head{left:1022px;top:43px}
.social.head span{background:var(--blue-light)}
.social.head span:nth-child(4){background:var(--orange)}
.callus{right:48px;top:84px;font-family:"Questrial",sans-serif;font-size:17px;color:var(--orange);display:flex;align-items:center;gap:8px}
.callus b{color:var(--blue);font-weight:400;font-size:18px;letter-spacing:1px}
.search{left:904px;top:130px;width:162px;height:30px;border:1px solid #cfcfcf;border-radius:3px;font-size:11px;color:#aaa;padding:8px 10px}
.find{left:1074px;top:130px;width:78px;height:30px;background:var(--orange);border-radius:3px;color:var(--white);font-size:14px;display:flex;align-items:center;justify-content:center;gap:5px}
.nav{left:48px;top:178px;width:1104px;height:44px;background:linear-gradient(#1b8ccc,#0a6fae);border-radius:4px;display:flex;align-items:center;justify-content:space-around;padding:0 12px}
.nav a{font-family:"Questrial",sans-serif;color:var(--white);text-decoration:none;font-size:15px;letter-spacing:1.4px;flex:1;text-align:center;border-left:1px solid rgba(255,255,255,.25)}
.nav a:first-child{border-left:none}
.greyband{left:0;top:600px;width:1200px;height:434px;background:var(--grey-bg)}
.hero{left:48px;top:233px;width:1104px;height:409px;background:linear-gradient(110deg,#dfe6ec,#f4f5f6 40%,#c9c3bd 65%,#e6dfd8)}
.mission{left:83px;top:384px;width:378px;height:203px;background:rgba(11,120,186,.92);color:var(--white);padding:24px 28px}
.mission h2{font-family:"Questrial",sans-serif;font-weight:400;font-size:23px;letter-spacing:1px;margin-bottom:6px}
.mission p{font-size:14px;line-height:20px}
.btn{background:var(--orange);color:var(--white);display:flex;align-items:center;justify-content:center}
.mission-more{left:83px;top:587px;width:114px;height:30px;font-size:14px}
.heading{font-family:"Questrial",sans-serif;font-size:21px;letter-spacing:1.2px;color:var(--blue)}
.heading em{font-style:normal;color:var(--orange)}
.rule{height:1px;background:var(--rule)}
.photo{border:3px solid #d7d7d7}
.welcome-img{left:85px;top:742px;width:410px;height:231px;background:linear-gradient(135deg,#2a2f36,#e8e9ea 45%,#1d3f78 70%,#c9c9c9)}
.welcome-text{left:543px;top:747px;width:565px;font-size:15.5px;line-height:20.6px;text-align:justify}
.welcome-text p+p{margin-top:20px}
.dots{left:1068px;top:1092px;display:flex;gap:5px}
.dots span{width:10px;height:10px;border-radius:50%;background:var(--blue)}
.dots span:first-child{background:var(--orange)}
.service{width:317px}
.service .photo{width:317px;height:211px}
.service h3{font-family:"Questrial",sans-serif;font-weight:400;color:var(--blue);font-size:18px;letter-spacing:.8px;margin-top:17px}
.service p{font-size:12.6px;line-height:17px;margin-top:8px;text-align:justify}
.service .btn{width:91px;height:27px;font-size:12px;margin-top:17px}
.clients{left:0;top:1643px;width:1200px;height:165px;background:var(--band);display:flex;align-items:center;justify-content:space-around;padding:0 110px}
.clients span{font-family:"Open Sans",sans-serif;font-weight:700;font-size:32px;color:#a3a3a3}
.footer{left:0;top:1808px;width:1200px;height:381px;background:var(--blue)}
.fhead{font-family:"Questrial",sans-serif;color:var(--white);font-size:16px;letter-spacing:1.3px;top:1844px}
.frule{height:1px;background:rgba(255,255,255,.3);top:1887px}
.post{left:95px;width:402px;display:flex;gap:10px;color:var(--white)}
.post .thumb{width:130px;height:93px;border:3px solid #dfe7ee;background:linear-gradient(135deg,#f4f4f4,#b7c4d0 60%,#3b4a5a)}
.post h4{font-size:15px;letter-spacing:.8px;font-weight:700}
.post p{font-size:13.5px;line-height:16px}
.post .more{font-size:13.5px;margin-top:6px}
.viewall{left:98px;top:2138px;color:var(--white);font-family:"Questrial",sans-serif;font-size:16px;letter-spacing:1.3px}
.quick{left:590px;top:1906px;list-style:none;color:var(--white);font-size:14px;line-height:30.5px}
.quick li::before{content:"›";margin-right:8px}
.contact{left:876px;color:var(--white);font-size:14px;line-height:16px;display:flex;gap:10px}
.contact svg{flex:none;margin-top:1px}
.footlogo{left:867px;top:2061px;width:210px;height:88px;background:var(--white);display:flex;align-items:center;justify-content:center;gap:8px;font-weight:700;color:var(--blue);font-size:30px}
.footlogo .dot{width:12px;height:12px;border-radius:50%;background:var(--orange)}
.bottombar{left:0;top:2189px;width:1200px;height:41px;background:var(--blue-dark);color:var(--white);font-size:13px}
.bottombar .links{position:absolute;left:98px;top:12px;word-spacing:4px}
.bottombar .copy{position:absolute;left:476px;top:12px}
.social.foot{position:absolute;left:952px;top:7px}
.social.foot span{background:var(--white)}
</style>
</head>
<body>
<div class="abs topline"></div>

<header>
  <div class="abs brand"><span class="dot"></span><div>Tevlora<small>INSIGHT</small></div></div>
  <div class="abs social head" aria-label="Social links"><span></span><span></span><span></span><span></span></div>
  <div class="abs callus">
    <svg width="14" height="14" viewBox="0 0 24 24"><path fill="#f79020" d="M6.6 10.8a15 15 0 0 0 6.6 6.6l2.2-2.2a1 1 0 0 1 1-.25 11.4 11.4 0 0 0 3.6.6 1 1 0 0 1 1 1V20a1 1 0 0 1-1 1A17 17 0 0 1 3 4a1 1 0 0 1 1-1h3.5a1 1 0 0 1 1 1c0 1.25.2 2.45.6 3.6a1 1 0 0 1-.25 1z"/></svg>
    Call us: <b>111-111-1111</b>
  </div>
  <div class="abs search">Keyword Search</div>
  <div class="abs find btn">Find
    <svg width="11" height="11" viewBox="0 0 12 12"><circle cx="5" cy="5" r="3.5" fill="none" stroke="#fff" stroke-width="1.6"/><path d="M7.6 7.6 11 11" stroke="#fff" stroke-width="1.8"/></svg>
  </div>
  <nav class="abs nav">
    <a>HOME</a><a>WHO WE ARE</a><a>OUR VALUES</a><a>WHAT WE DO</a><a>OUR CLIENTS</a><a>BLOG</a><a>USEFUL LINKS</a><a>CONTACT</a>
  </nav>
</header>

<div class="abs greyband"></div>
<section>
  <div class="abs hero" role="img" aria-label="Photo of a business meeting with colleagues around a table"></div>
  <div class="abs mission">
    <h2>OUR MISSION</h2>
    <p>Lorem ipsum dolor sit amet, consectetur adipiscing elit. Phasellus eget leo leo. Sed adipiscing mi orci, vel ultrices turpis mattis a. Quisque sed eros luctus, euismod ligula et, suscipit dolor. Sed suscipit tortor eget leo hendrerit semper.</p>
  </div>
  <div class="abs btn mission-more">Read more +</div>
</section>

<section>
  <h2 class="abs heading" style="left:83px;top:678px">WELCOME TO <em>TEVLORA INSIGHTS</em></h2>
  <div class="abs rule" style="left:83px;top:717px;width:1035px"></div>
  <div class="abs photo welcome-img" role="img" aria-label="Photo of hands working with a laptop and documents on a meeting table"></div>
  <div class="abs welcome-text">
    <p>Lorem ipsum dolor sit amet, consectetur adipiscing elit. Phasellus eget leo leo. Sed adipiscing mi orci, vel ultrices turpis mattis a. Quisque sed eros luctus, euismod ligula et, suscipit dolor. Sed suscipit tortor eget leo hendrerit semper. Sed et fermentum erat.</p>
    <p>Curabitur tristique vestibulum bibendum. Quisque eget varius eros. Nunc id laoreet sem. Nullam vulputate fringilla mi sit amet imperdiet. Lorem ipsum dolor sit amet, consectetur adipiscing elit. Pellentesque habitant morbi tristique senectus et netus et malesuada fames ac turpis egestas.</p>
  </div>
</section>

<section>
  <h2 class="abs heading" style="left:83px;top:1078px">WHAT <em>WE</em> DO</h2>
  <div class="abs dots"><span></span><span></span><span></span></div>
  <div class="abs rule" style="left:83px;top:1115px;width:1035px"></div>

  <article class="abs service" style="left:85px;top:1151px">
    <div class="photo" role="img" aria-label="Photo of two business people in a meeting" style="background:linear-gradient(#e9eef3,#c5ccd3 55%,#6b5a4c)"></div>
    <h3>Governance</h3>
    <p>Lorem ipsum dolor sit amet, consectetur adipiscing elit. Curabitur lacinia pretium risus ac euismod.Arabitur lorem lacinia pretium risus ac ipsum dolor sit amet consectetur adi.</p>
    <div class="btn">read more</div>
  </article>
  <article class="abs service" style="left:442px;top:1151px">
    <div class="photo" role="img" aria-label="Illustration of a person surrounded by floating digital screens" style="background:radial-gradient(circle at 50% 55%,#ffffff,#8ec6ea 55%,#3f7fb8)"></div>
    <h3>Information Technology Insight</h3>
    <p>Lorem ipsum dolor sit amet, consectetur adipiscing elit. Curabitur lacinia pretium risus ac euismod.Arabitur lorem lacinia pretium risus ac ipsum dolor sit amet consectetur adi.</p>
    <div class="btn">read more</div>
  </article>
  <article class="abs service" style="left:799px;top:1151px">
    <div class="photo" role="img" aria-label="Photo of a calculator and pen on a financial report" style="background:linear-gradient(135deg,#5e6b78,#b9c6d3 50%,#eef2f6)"></div>
    <h3>Financial Management Insight</h3>
    <p>Lorem ipsum dolor sit amet, consectetur adipiscing elit. Curabitur lacinia pretium risus ac euismod.Arabitur lorem lacinia pretium risus ac ipsum dolor sit amet consectetur adi.</p>
    <div class="btn">read more</div>
  </article>
</section>

<section class="abs clients" aria-label="Our clients">
  <span>Norvane</span><span>Kestrel</span><span>Orbiq</span><span>Lumerra</span><span>Daxton</span>
</section>

<footer>
  <div class="abs footer"></div>
  <h3 class="abs fhead" style="left:94px">LATEST BLOG</h3>
  <h3 class="abs fhead" style="left:574px">QUICKLINKS</h3>
  <h3 class="abs fhead" style="left:870px">CONTACT INFO</h3>
  <div class="abs frule" style="left:94px;width:403px"></div>
  <div class="abs frule" style="left:574px;width:205px"></div>
  <div class="abs frule" style="left:870px;width:208px"></div>

  <article class="abs post" style="top:1900px">
    <div class="thumb" role="img" aria-label="Photo of a presenter beside a chart board"></div>
    <div><h4>Article Title goes here</h4><p>Lorem ipsum dolor sit amet, consectetur adipiscing elit dolor sit amet sit amet, consectetur.</p><div class="more">Read more +</div></div>
  </article>
  <div class="abs frule" style="left:94px;width:403px;top:2005px"></div>
  <article class="abs post" style="top:2022px">
    <div class="thumb" role="img" aria-label="Photo of a presenter beside a chart board"></div>
    <div><h4>Article Title goes here</h4><p>Lorem ipsum dolor sit amet, consectetur adipiscing elit dolor sit amet sit amet, consectetur.</p><div class="more">Read more +</div></div>
  </article>
  <div class="abs frule" style="left:94px;width:403px;top:2127px"></div>
  <div class="abs viewall">VIEW ALL ARTICLES</div>

  <ul class="abs quick">
    <li>Home</li><li>About us</li><li>Case Studies</li><li>News</li><li>Our Clients</li><li>Contact us</li>
  </ul>
  <div class="abs frule" style="left:574px;width:205px;top:2127px"></div>

  <div class="abs contact" style="top:1909px">
    <svg width="14" height="18" viewBox="0 0 14 18"><path fill="none" stroke="#fff" stroke-width="1.8" d="M7 17S1.5 10.5 1.5 6.5a5.5 5.5 0 0 1 11 0C12.5 10.5 7 17 7 17z"/><circle cx="7" cy="6.5" r="2" fill="#fff"/></svg>
    <div>1344 Your Address<br>Location here, NY<br>Country name</div>
  </div>
  <div class="abs contact" style="top:1973px">
    <svg width="16" height="14" viewBox="0 0 16 14"><path fill="#fff" d="M1 4c0-2 3-3 7-3s7 1 7 3v1h-3V4H4v1H1zM3 7h10l1 6H2z"/><circle cx="8" cy="10" r="1.6" fill="#0b78ba"/></svg>
    <div>111-111-1111</div>
  </div>
  <div class="abs contact" style="top:2022px">
    <svg width="16" height="12" viewBox="0 0 16 12"><rect width="16" height="12" rx="1" fill="#fff"/><path d="M1 1l7 6 7-6" fill="none" stroke="#0b78ba" stroke-width="1.3"/></svg>
    <div>youremail@mail.com</div>
  </div>
  <div class="abs footlogo"><span class="dot"></span>Tevlora</div>

  <div class="abs bottombar">
    <div class="links">Sitemap &nbsp;|&nbsp; FAQ &nbsp;|&nbsp; Privacy Policy</div>
    <div class="copy">Copyright 2014 · All rights reserved</div>
    <div class="social foot" aria-label="Social links"><span></span><span></span><span></span><span></span></div>
  </div>
</footer>
</body>
</html>
```